Business Card Design For Office Furniture Clearance Company

Kestrel Office Clearance - our company name pretty much explains what we do, we clear offices for high end clients, mainly plc's and large international companies.

We require a nice looking business card that displays professionalism but without being too serious.

It would be nice to see just a little more than a conventional boring business card, make sure you add some flare.

Industry/Entity Type

Office Furniture

Contact Information for Business Card

CARD 1

Mark Holloway
Director
mark@kestrelofficeclearance.co.uk
m: 07700 153928

t: 01632 960418
www.kestrelofficeclearance.co.uk

Kestrel Office Clearance
Unit K4 B
2-8 Fenwick Lane
Harwick
Eastmoor
ZZ9 4QT

no-cost office clearances… nothing could be simpler.

CARD 2

Peter Radford
Director
peter@kestrelofficeclearance.co.uk
m: 07700 382615

t: 01632 960418

Kestrel Office Clearance
Unit K4 B
2-8 Fenwick Lane
Harwick
Eastmoor
ZZ9 4QT

Font styles to use
Sans Serif

Requirements
Must have
• A white background - as we have a blue logo.
Nice to have
• Nice use of the logo - play around with this and dissect it.

```html
<!DOCTYPE html>
<html lang="en">
<head>
<meta charset="utf-8">
<title>Kestrel Office Clearance – Business Card</title>
<link rel="stylesheet" href="https://fonts.googleapis.com/css2?family=Open+Sans:wght@400;600;700&display=swap">
<style>
  :root {
    --stage: #eceef0;
    --card-blue: #1b71b1;
    --card-blue-soft: #2a80be;
    --card-blue-faint: #3a8bc6;
    --brand-blue: #0f78c0;
    --paper: #f9f9f9;
    --ink-light: #ffffff;
    --ink-muted: #e3eef7;
  }
  * { margin: 0; padding: 0; box-sizing: border-box; }
  html, body {
    width: 1200px; height: 900px; overflow: hidden;
    background: var(--stage);
    font-family: "Open Sans", Arial, sans-serif;
  }
  .canvas { position: relative; width: 1200px; height: 900px; }

  .card {
    position: absolute;
    box-shadow: 0 6px 18px rgba(0,0,0,0.18);
  }

  /* Front */
  .card-front {
    left: 238px; top: 60px; width: 555px; height: 345px;
    background: var(--card-blue);
    color: var(--ink-light);
  }
  .holder { position: absolute; left: 32px; top: 40px; }
  .holder-name { font-size: 19px; font-weight: 600; line-height: 22px; }
  .holder-role { font-size: 14px; font-weight: 400; color: var(--ink-muted); line-height: 17px; }

  .company { position: absolute; left: 33px; top: 99px; }
  .company-name { font-size: 17px; font-weight: 700; line-height: 22px; }
  .company-address { font-size: 14.5px; font-weight: 400; line-height: 20px; color: var(--ink-muted); }

  .contacts { position: absolute; left: 34px; top: 180px; list-style: none; }
  .contacts li {
    display: flex; align-items: center; gap: 9px;
    font-size: 14.5px; line-height: 20px; color: var(--ink-muted);
  }
  .contacts svg { width: 11px; height: 11px; fill: var(--ink-light); flex: none; }

  .tagline {
    position: absolute; left: 32px; top: 278px;
    font-size: 15.5px; font-weight: 600;
  }

  .brand-mark-faint {
    position: absolute; left: 318px; top: 43px; width: 200px; height: 200px;
    border-radius: 50%;
    background: var(--card-blue-soft);
    border: 1px solid var(--card-blue-faint);
    display: flex; align-items: center; justify-content: center;
  }
  .brand-mark-faint span {
    font-size: 26px; font-weight: 700; color: var(--card-blue-faint);
  }

  /* Back */
  .card-back {
    left: 457px; top: 518px; width: 560px; height: 344px;
    background: var(--paper);
    display: flex; flex-direction: column; align-items: center; justify-content: center;
    gap: 16px;
  }
  .brand-circle {
    width: 160px; height: 160px; border-radius: 50%;
    background: var(--brand-blue);
  }
  .brand-name {
    font-size: 22px; font-weight: 700; color: var(--brand-blue);
  }
</style>
</head>
<body>
<main class="canvas">

  <section class="card card-front" aria-label="Business card front">
    <div class="brand-mark-faint"><span>Kestrel</span></div>

    <div class="holder">
      <p class="holder-name">Mark Holloway</p>
      <p class="holder-role">Director</p>
    </div>

    <div class="company">
      <p class="company-name">Kestrel Office Clearance</p>
      <p class="company-address">Unit K4 B,2-8 Fenwick Lane</p>
      <p class="company-address">Harwick,Eastmoor,ZZ9 4QT</p>
    </div>

    <ul class="contacts">
      <li>
        <svg viewBox="0 0 12 12" aria-hidden="true"><path d="M3 0h6a1 1 0 0 1 1 1v10a1 1 0 0 1-1 1H3a1 1 0 0 1-1-1V1a1 1 0 0 1 1-1zm0.5 1.5v7.5h5V1.5zM6 10a.6.6 0 1 0 0 1.2A.6.6 0 0 0 6 10z"/></svg>
        07700 153928
      </li>
      <li>
        <svg viewBox="0 0 12 12" aria-hidden="true"><path d="M2.4 0.5l2 2.2-1 1.3c.8 1.6 2 2.8 3.6 3.6l1.3-1 2.2 2-1 2.3C5 10.5 1.5 7 0.1 1.5z"/></svg>
        01632 960418
      </li>
      <li>
        <svg viewBox="0 0 12 12" aria-hidden="true"><path d="M0 2.5h12v7H0zM0.8 3l5.2 3.6L11.2 3z" fill-rule="evenodd"/></svg>
        mark@kestrelofficeclearance.co.uk
      </li>
      <li>
        <svg viewBox="0 0 12 12" aria-hidden="true"><circle cx="6" cy="6" r="5.5"/><path d="M1 6h10M6 0.5c-2 2-2 9 0 11M6 0.5c2 2 2 9 0 11" stroke="#1b71b1" stroke-width="0.9" fill="none"/></svg>
        www.kestrelofficeclearance.co.uk
      </li>
    </ul>

    <p class="tagline">no-cost office clearances… nothing could be simpler.</p>
  </section>

  <section class="card card-back" aria-label="Business card back">
    <div class="brand-circle"></div>
    <p class="brand-name">Kestrel Office Clearance</p>
  </section>

</main>
</body>
</html>
```